Letterhead Design for Law Firm

**Edit: I have added the photo of a bottom that I like.

------
We are looking for a re-design of our new letterhead. The letterhead is for a law firm and will be used for digital and traditionally printed correspondence.

Here are some suggestions:

- Please use colours are #8ec900 and simple black.
- Please do not use any type of "waves" at the bottom of the page. This is not in style at all.
- Please stay modern yet conservative.
- Please use font Segoe UI Light or similar if you can
- Avoid clipart or illustrations.
- Utilize ample white space in the layout so the design looks clean and information is easy to read at a glance. Don't overcrowd the letterhead.
- Make sure the letterhead design is consistent with our brand identity (see corvelith.ca)
-Please, no black headers or footers.

I am attaching my current letterhead and signature for your convenience.

Remember, the letterhead is an extension of our professional identity. We are a successful firm and trial lawyers who correspond with insurers, judges, lawyers, courts, clients, etc. Make it new, modern, attractive, yet powerful and conservative.

It needs to be easily printable. I would like the bleed removed in print so the black bar the bottom crosses the page (but the text is not near the edges)
Updates

Low design quality

Target Market(s)

Clients, Government Offices, Judiciary, Lawyers, Insurance Companies, Colleagues.

Industry/Entity Type

Law

Other font styles liked:
• Segoe UI LIght, Calibri Light,

Colors
00AB8E
00BBA5
67D7C9
C6EFE9
E9F9F6

Requirements
Must have
• Everything that is on the letterhead now.
Nice to have
• Cutting Edge design, yet conservative.
Should not have
• law firm cliche design, images,

```html
<!DOCTYPE html>
<html lang="en">
<head>
<meta charset="utf-8">
<title>Varenne Personal Injury Lawyers – Letterhead</title>
<link rel="stylesheet" href="https://fonts.googleapis.com/css2?family=Open+Sans:wght@400;600&family=Cinzel:wght@400&display=swap">
<style>
  :root {
    --brand-green: #8ec900;
    --ink: #111111;
    --watermark: #d5d4d4;
    --paper: #ffffff;
    --backdrop: #e6e7e8;
  }
  * { margin: 0; padding: 0; box-sizing: border-box; }
  html, body { width: 1200px; height: 1200px; overflow: hidden; }
  body {
    background: var(--backdrop);
    font-family: "Open Sans", "Segoe UI", sans-serif;
    color: var(--ink);
    position: relative;
  }
  .letterhead {
    position: absolute;
    left: 366px; top: 197px;
    width: 689px; height: 891px;
    background: var(--paper);
    box-shadow: 0 2px 14px rgba(0,0,0,.12);
    overflow: hidden;
  }
  .brand {
    position: absolute; left: 25px; top: 30px;
    width: 235px; text-align: center;
  }
  .brand-name {
    font-family: "Open Sans", sans-serif;
    font-weight: 400;
    font-size: 48px; line-height: 1;
    letter-spacing: 1px;
    color: var(--ink);
  }
  .brand-tagline {
    margin-top: 8px;
    font-family: "Cinzel", serif;
    font-size: 13px; letter-spacing: .6px;
    color: var(--ink);
  }
  .side-mark {
    position: absolute; left: 486px; top: 8px;
  }
  .closing {
    position: absolute; left: 24px; top: 618px;
    font-size: 10px; line-height: 14px;
  }
  .signature {
    display: block; width: 180px; height: 34px; margin: 8px 0 10px;
    background: linear-gradient(90deg, rgba(17,17,17,.18), rgba(17,17,17,.06));
    border-radius: 2px;
  }
  .contact {
    position: absolute; left: 24px; top: 753px;
    font-size: 12px; line-height: 18.5px;
  }
  .label { color: var(--brand-green); font-weight: 600; }
  .practice {
    position: absolute; left: 24px; top: 816px; width: 497px;
    font-size: 12.5px; line-height: 18.5px;
  }
  .practice-heading {
    display: flex; align-items: center; gap: 6px;
    color: var(--brand-green); font-weight: 600; font-size: 12px;
  }
  .practice-heading::after {
    content: ""; flex: 1; height: 1px; background: var(--brand-green); margin-top: 3px;
  }
</style>
</head>
<body>
  <main class="letterhead">
    <header class="brand">
      <div class="brand-name">VARENNE</div>
      <div class="brand-tagline">Personal Injury Lawyers</div>
    </header>

    <svg class="side-mark" width="200" height="875" viewBox="0 0 200 875" aria-hidden="true">
      <text transform="translate(196 870) rotate(-90)" textLength="862" lengthAdjust="spacingAndGlyphs"
            font-family="Open Sans, sans-serif" font-size="262" fill="var(--watermark)">VARENNE</text>
    </svg>

    <section class="closing">
      <p>Yours Very Truly,<br>VARENNE PERSONAL INJURY LAWYERS</p>
      <span class="signature" role="img" aria-label="Handwritten signature of Paul R. Varenne"></span>
      <p>Paul R. Varenne<br>Varenne Law Professional Corporation/hh Encl.</p>
    </section>

    <section class="contact">
      <p><span class="label">File Clerk:</span> Claire Dunmore</p>
      <p>48 Harbour Street W., Suite 1205, Hamilton, ON&nbsp; L8R 2B6</p>
      <p><span class="label">T:</span> 905-555-0142&nbsp; / <span class="label">F:</span> 905-555-0187/ <span class="label">E:</span> claire@corvelith.ca / <span class="label">W:</span> www.CORVELITH.ca</p>
    </section>

    <section class="practice">
      <h2 class="practice-heading">Practice Restricted</h2>
      <p>Serious Personal Injury / Wrongful Death Litigation / Long-Term Disability Litigation<br>
      Wrongful Dismissal Litigation / Employee Terminations</p>
    </section>
  </main>
</body>
</html>
```